So the ones in the picture are my original cards that I came up with. 😅however I kinda messed up on two things, I missed spelled my name it should be Marcello Vandora as well as the email should be Marcellov@brightlanecrews.com. I would like to clean this card up and also make it pop! Something that people would remember me by and that screams DEMOLITION. As well as a card that give you a feeling of loyalty and trust. I would also like to change and remove junk hauling and add full demolition to replace it. These cards worked for a little while but I cant make that my image while handing these out. I would also like to only put down that we are located in Laguna Vista, CA, 92000 instead of the address on the card. Also if we can have a line that states Licensed, Bonded, & Insured. With out License # 4837215

Target Market(s)

Contractors and Home owners

Industry/Entity Type

Construction specialist in Demolition

Contact Information for Business Card

R Wrecking Selective Demolition & Full Demolition Kitchens AD Preparation Bathrooms Sheds Interiors & Exteriors Demo Digging And Much More Marcello Vandora Owner our city state and zip

Font styles to use
Serif
Sans Serif
Decorative

Colors
0054AA
0677BA
7BADD7
CADEEF
E8F1F8
0094D4
00A9DD
6FCCEA
C7EBF8
E9F6FB

Requirements
Must have
• License# 4837215
Nice to have
• Trying to go with a blue and white color scheme
Should not have
• Building construction

```html
<!DOCTYPE html>
<html lang="en">
<head>
<meta charset="utf-8">
<title>RK Wrecking – Business Cards</title>
<link href="https://fonts.googleapis.com/css2?family=Open+Sans:wght@400;600;700&family=Oswald:wght@500;700&display=swap" rel="stylesheet">
<style>
  :root {
    --brand-blue: #0b4d9b;
    --ink: #111111;
    --paper: #f4f4f4;
    --paper-white: #ffffff;
    --backdrop: #2a2a2c;
  }
  * { margin: 0; padding: 0; box-sizing: border-box; }
  html, body { width: 1200px; height: 780px; overflow: hidden; }
  body {
    background: var(--backdrop);
    font-family: "Open Sans", Arial, sans-serif;
    position: relative;
  }
  .card {
    position: absolute;
    width: 520px;
    height: 300px;
    overflow: hidden;
    border-radius: 3px;
    box-shadow: 0 10px 24px rgba(0,0,0,.45);
  }

  /* Contact card */
  .contact-card { left: 50px; top: 240px; background: var(--paper); }
  .contact-card .wave { position: absolute; inset: 0; }
  .brand {
    position: absolute;
    display: flex;
    align-items: center;
    gap: 10px;
    color: var(--brand-blue);
    font-weight: 700;
    font-size: 30px;
    letter-spacing: .5px;
    white-space: nowrap;
  }
  .brand-dot {
    width: 18px; height: 18px; border-radius: 50%;
    background: var(--brand-blue);
  }
  .contact-card .brand { left: 26px; top: 18px; }
  .license {
    position: absolute;
    font-weight: 700;
    font-size: 12px;
    color: var(--ink);
    letter-spacing: .5px;
    white-space: nowrap;
  }
  .contact-card .license { left: 54px; top: 62px; }
  .person { position: absolute; right: 26px; top: 92px; text-align: right; }
  .person-name { color: var(--brand-blue); font-weight: 700; font-size: 24px; letter-spacing: .5px; line-height: 1.3; }
  .person-title { color: var(--ink); font-size: 13.5px; font-weight: 600; }
  .contact-list {
    position: absolute; right: 120px; bottom: 12px;
    list-style: none; text-align: right; color: var(--paper-white);
    font-size: 13px; line-height: 1.4;
  }
  .contact-list li { display: flex; justify-content: flex-end; align-items: center; gap: 8px; }
  .contact-list .location { margin-bottom: 4px; }
  .contact-list svg { width: 13px; height: 13px; flex: none; }
  .icon-spacer { width: 13px; flex: none; }

  /* Services card */
  .services-card { left: 630px; top: 240px; background: var(--paper-white); }
  .services-card .brand { left: 50%; transform: translateX(-50%); top: 26px; }
  .services-card .license { left: 50%; transform: translateX(-50%); top: 70px; }
  .band {
    position: absolute; left: 0; right: 0; top: 104px; height: 84px;
    background: var(--brand-blue); color: var(--paper-white); text-align: center;
    padding-top: 10px;
  }
  .band-title { font-weight: 700; font-size: 28px; letter-spacing: 1px; line-height: 1.3; }
  .band-tagline {
    font-family: "Oswald", "Arial Narrow", sans-serif; font-weight: 500;
    font-size: 13px; letter-spacing: .5px; text-transform: uppercase;
    word-spacing: 2px;
  }
  .band-tagline .gap { display: inline-block; width: 22px; }
  .service-list {
    position: absolute; left: 0; right: 0; top: 204px;
    text-align: center; color: var(--ink); font-size: 15px; line-height: 1.6;
  }
  .service-list .bullet { color: var(--brand-blue); margin: 0 4px; }
  .credentials {
    position: absolute; left: 0; right: 0; top: 264px;
    text-align: center; color: var(--brand-blue);
    font-weight: 700; font-size: 13px; letter-spacing: 1px; text-transform: uppercase;
  }
</style>
</head>
<body>

  <section class="card contact-card">
    <svg class="wave" viewBox="0 0 520 300" preserveAspectRatio="none" aria-hidden="true">
      <path d="M0 86 C20 150 80 160 200 165 C330 170 430 180 480 240 C495 260 505 285 510 300 L0 300 Z" fill="var(--brand-blue)"/>
      <path d="M0 74 C22 140 82 148 200 153 C330 158 440 168 492 232 C506 252 514 278 518 300" fill="none" stroke="var(--ink)" stroke-width="5"/>
    </svg>

    <div class="brand"><span class="brand-dot"></span>RK Wrecking</div>
    <div class="license">LICENSE#4837215</div>

    <div class="person">
      <div class="person-name">Marcello Vandora</div>
      <div class="person-title">Owner our city state and zip</div>
    </div>

    <ul class="contact-list">
      <li class="location">Laguna Vista,<br>CA, 92000<span class="icon-spacer"></span></li>
      <li>(949) 555-0182
        <svg viewBox="0 0 16 16"><path d="M3 1 L6 1 L7 5 L5 6.5 C6 9 7 10 9.5 11 L11 9 L15 10 L15 13 C15 14 14 15 13 15 C6 15 1 10 1 3 C1 2 2 1 3 1 Z" fill="currentColor"/></svg>
      </li>
      <li>info@brightlanecrews.com
        <svg viewBox="0 0 16 16"><circle cx="8" cy="8" r="6.5" fill="none" stroke="currentColor" stroke-width="1.4"/><ellipse cx="8" cy="8" rx="3" ry="6.5" fill="none" stroke="currentColor" stroke-width="1.2"/><line x1="1.5" y1="8" x2="14.5" y2="8" stroke="currentColor" stroke-width="1.2"/></svg>
      </li>
      <li>Marcellov@brightlanecrews.com
        <svg viewBox="0 0 16 16"><rect x="1" y="3" width="14" height="10" rx="1" fill="none" stroke="currentColor" stroke-width="1.4"/><path d="M1.5 3.5 L8 9 L14.5 3.5" fill="none" stroke="currentColor" stroke-width="1.4"/></svg>
      </li>
    </ul>
  </section>

  <section class="card services-card">
    <div class="brand"><span class="brand-dot"></span>RK Wrecking</div>
    <div class="license">LICENSE#4837215</div>

    <div class="band">
      <div class="band-title">R Wrecking</div>
      <div class="band-tagline">R Wrecking Selective Demolition<span class="gap"></span>Full Demolition</div>
    </div>

    <div class="service-list">
      <div><span class="bullet">●</span>Sheds <span class="bullet">●</span>Digging <span class="bullet">●</span>Kitchens <span class="bullet">●</span>Bathrooms</div>
      <div><span class="bullet">●</span>AD Preparation <span class="bullet">●</span>Interiors &amp; Exteriors Demo</div>
    </div>

    <div class="credentials">Licensed, Bonded, &amp; Insured</div>
  </section>

</body>
</html>
```